Brell Stone Company Business Cards

Front and Back Business Card - logo and text setup - cool design. I need workable photoshop or illustrator files so I can setup each employee card with design that is created
Updates

Hi everyone, thank you for the great entries. Please no more white and blue cards - there are so many already - black and silver only now please. thanks!

Target Market(s)

Construction Industry - Facility Managers

Industry/Entity Type

Construction

Contact Information for Business Card

I really like contemporary simplistic looks - clean neat....not opposed to seeing some black backrounds

Requirements
Must have
• Logo/website address with design on front only - www.brellstone-example.com (logo attached)
• Back:
• Name/Title/Company Address/Phone/email address
Nice to have
• Cool design
Should not have
• Nothing gimmicky like Fire or Water - since we are a Fire Protection company - it has all been done

```html
<!DOCTYPE html>
<html lang="en">
<head>
<meta charset="utf-8">
<title>Brell Stone Company Business Cards</title>
<link href="https://fonts.googleapis.com/css2?family=Poppins:wght@400;500;700;800&display=swap" rel="stylesheet">
<style>
  :root {
    --black: #151617;
    --silver: #c5c8cc;
    --silver-dark: #8b8f95;
    --paper: #eeeff0;
    --ink: #3a3c3f;
    --backdrop: #e2e2e0;
  }
  * { box-sizing: border-box; margin: 0; padding: 0; }
  html, body {
    width: 1200px; height: 920px; overflow: hidden;
    background: var(--backdrop);
    font-family: "Poppins", sans-serif;
  }
  .stage { position: relative; width: 1200px; height: 920px; }
  .card {
    position: absolute; top: 311px;
    width: 536px; height: 298px;
    box-shadow: 0 4px 12px rgba(0,0,0,0.2);
  }
  .card-front { left: 46px; background: var(--black); }
  .card-back { left: 618px; background: var(--paper); }

  .wordmark {
    position: absolute;
    font-weight: 800; letter-spacing: -1px; line-height: 1;
    white-space: nowrap;
  }
  .card-front .wordmark {
    left: 0; right: 0; top: 112px; text-align: center;
    font-size: 50px; color: var(--silver);
  }
  .card-front .website {
    position: absolute; left: 0; right: 0; top: 258px; text-align: center;
    font-size: 13px; letter-spacing: 1px; color: var(--silver);
  }
  .card-back .wordmark {
    left: 38px; top: 130px; font-size: 36px; color: var(--black);
  }
  .divider {
    position: absolute; left: 262px; top: 72px; height: 158px;
    border-left: 2px dashed var(--silver-dark);
  }
  .details { position: absolute; left: 282px; top: 70px; color: var(--ink); }
  .person-name {
    font-size: 17px; font-weight: 500; color: var(--black);
    letter-spacing: 0.5px; line-height: 22px;
  }
  .role, .address { font-size: 12px; line-height: 20px; }
  .role { margin-bottom: 2px; }
  .address { margin-bottom: 4px; }
  .contact-list { list-style: none; font-size: 12.5px; }
  .contact-list li { display: flex; align-items: center; height: 19px; white-space: nowrap; }
  .contact-list svg {
    width: 11px; height: 11px; margin-right: 9px; flex: none;
    color: var(--silver-dark); fill: currentColor;
  }
</style>
</head>
<body>
<main class="stage">
  <section class="card card-front" aria-label="Card front">
    <div class="wordmark">Brell Stone</div>
    <div class="website">www.brellstone-example.com</div>
  </section>

  <section class="card card-back" aria-label="Card back">
    <div class="wordmark">Brell Stone</div>
    <div class="divider"></div>
    <div class="details">
      <h1 class="person-name">DANA WHITCOMBE</h1>
      <p class="role">Senior Consultant</p>
      <p class="address">48 Harbor Lane<br>Westfield, NY 11950</p>
      <ul class="contact-list">
        <li>
          <svg viewBox="0 0 12 12" aria-hidden="true"><path d="M2.4 0.6 4.4 2.6 3.3 4.1C4 5.6 6.3 7.9 7.9 8.7L9.4 7.6 11.4 9.6 10 11.4C5.4 11.2 0.8 6.6 0.6 2Z"/></svg>
          (555) 214-3307
        </li>
        <li>
          <svg viewBox="0 0 12 12" aria-hidden="true"><rect x="3" y="0.5" width="6" height="3"/><rect x="0.5" y="4" width="11" height="5" rx="1"/><rect x="3" y="7.5" width="6" height="4" fill="#eeeff0" stroke="currentColor" stroke-width="1"/></svg>
          (555) 214-3308
        </li>
        <li>
          <svg viewBox="0 0 12 12" aria-hidden="true"><rect x="0.5" y="2" width="11" height="8" fill="none" stroke="currentColor" stroke-width="1.2"/><path d="M0.8 2.4 6 6.6 11.2 2.4" fill="none" stroke="currentColor" stroke-width="1.2"/></svg>
          info@brellstone-example.com
        </li>
        <li>
          <svg viewBox="0 0 12 12" aria-hidden="true"><circle cx="6" cy="6" r="5.3" fill="none" stroke="currentColor" stroke-width="1.2"/><ellipse cx="6" cy="6" rx="2.2" ry="5.3" fill="none" stroke="currentColor" stroke-width="1"/><path d="M0.8 6H11.2" stroke="currentColor" stroke-width="1"/></svg>
          www.brellstone-example.com
        </li>
      </ul>
    </div>
  </section>
</main>
</body>
</html>
```